Corvane Card

The logo is the Spanish flag colors I want a vibrant eye catching design with the yellow / red colors over either Navy or white background or black even ,
Would like a 2D feel to the logo with another lighter color logo under it look ,

Contact Information for Business Card

Corvane Flooring
Teodor Vashkin
Main Number
Cell Number
Fax Number

Website on the side of the card somewhere

Font styles to use
Sans Serif

Colors
ec1f27
ffc214

Requirements
Must have
• 2 logos feel one is bolder and the other one underneath very light

```html
<!DOCTYPE html>
<html lang="en">
<head>
<meta charset="utf-8">
<title>Corvane Flooring – Business Card</title>
<link href="https://fonts.googleapis.com/css2?family=Catamaran:wght@700&family=Arimo:wght@400&display=swap" rel="stylesheet">
<style>
  :root {
    --brand-red: #ec1f27;
    --brand-yellow: #ffc214;
    --canvas-bg: #e9e7e5;
    --frost-light: #f4f4f4;
    --frost-mid: #dcdcdc;
    --contact-text: #ffffff;
  }
  html, body {
    margin: 0;
    padding: 0;
    width: 1200px;
    height: 900px;
    overflow: hidden;
    background: var(--canvas-bg);
  }
  .canvas {
    position: relative;
    width: 1200px;
    height: 900px;
  }
  .business-card {
    position: absolute;
    left: 100px;
    top: 140px;
    width: 1000px;
    height: 619px;
    background: var(--brand-red);
    overflow: hidden;
  }
  .yellow-band {
    position: absolute;
    left: 686px;
    top: 0;
    width: 314px;
    height: 100%;
    background: var(--brand-yellow);
  }
  .frost-circle {
    position: absolute;
    left: 415px;
    top: 44px;
    width: 532px;
    height: 532px;
    border-radius: 50%;
    background: radial-gradient(circle at 45% 40%, var(--frost-light) 0%, #e6e6e6 55%, var(--frost-mid) 100%);
  }
  .brand-name {
    position: absolute;
    left: 415px;
    top: 44px;
    width: 532px;
    height: 532px;
    display: flex;
    flex-direction: column;
    align-items: center;
    justify-content: center;
    font-family: "Catamaran", sans-serif;
    font-weight: 700;
    color: var(--brand-red);
    padding-top: 110px;
    box-sizing: border-box;
  }
  .brand-mark {
    width: 46px;
    height: 46px;
    background: var(--brand-red);
    margin-bottom: 18px;
  }
  .brand-word {
    font-size: 60px;
    line-height: 1;
    letter-spacing: 1px;
  }
  .brand-tagline {
    font-size: 26px;
    line-height: 1;
    letter-spacing: 26px;
    margin-top: 14px;
    margin-right: -26px;
  }
  .person-name {
    position: absolute;
    left: 63px;
    top: 116px;
    margin: 0;
    font-family: "Catamaran", sans-serif;
    font-weight: 700;
    font-size: 40px;
    line-height: 1;
    color: var(--brand-yellow);
    letter-spacing: 0.5px;
  }
  .contact-list {
    position: absolute;
    left: 61px;
    top: 320px;
    margin: 0;
    padding: 0;
    list-style: none;
    font-family: "Arimo", sans-serif;
    font-size: 27px;
    color: var(--contact-text);
  }
  .contact-item {
    display: flex;
    align-items: center;
    height: 36.5px;
  }
  .contact-icon {
    width: 26px;
    height: 26px;
    margin-right: 9px;
    fill: var(--brand-yellow);
    flex-shrink: 0;
  }
  .contact-icon--outline {
    fill: none;
    stroke: var(--brand-yellow);
    stroke-width: 2.4;
    stroke-linejoin: round;
  }
</style>
</head>
<body>
<div class="canvas">
  <div class="business-card">
    <div class="yellow-band"></div>
    <div class="frost-circle"></div>

    <div class="brand-name" aria-label="Corvane Flooring">
      <div class="brand-mark"></div>
      <div class="brand-word">CORVANE</div>
      <div class="brand-tagline">FLOORING</div>
    </div>

    <h1 class="person-name">TEODOR VASHKIN</h1>

    <ul class="contact-list">
      <li class="contact-item">
        <svg class="contact-icon" viewBox="0 0 26 26" aria-hidden="true">
          <path d="M2 9c0-3 5-5 11-5s11 2 11 5v2h-5V8.5C17 8 15 7.8 13 7.8S9 8 7 8.5V11H2z"/>
          <path d="M6 12l2-3h10l2 3 2 8H4z"/>
        </svg>
        <span>312 478 2290</span>
      </li>
      <li class="contact-item">
        <svg class="contact-icon" viewBox="0 0 26 26" aria-hidden="true">
          <path d="M8 1h10a2 2 0 0 1 2 2v20a2 2 0 0 1-2 2H8a2 2 0 0 1-2-2V3a2 2 0 0 1 2-2zm0 4v15h10V5zm5 16.5a1.3 1.3 0 1 0 0 2.6 1.3 1.3 0 0 0 0-2.6z"/>
        </svg>
        <span>312 906 1547</span>
      </li>
      <li class="contact-item">
        <svg class="contact-icon" viewBox="0 0 26 26" aria-hidden="true">
          <path d="M7 2h12v6H7z"/>
          <path d="M3 9h20a2 2 0 0 1 2 2v8h-4v-4H5v4H1v-8a2 2 0 0 1 2-2z"/>
          <path d="M7 17h12v7H7z"/>
        </svg>
        <span>312 478 2291</span>
      </li>
      <li class="contact-item">
        <svg class="contact-icon contact-icon--outline" viewBox="0 0 26 26" aria-hidden="true">
          <rect x="2" y="6" width="22" height="14"/>
          <path d="M2 6l11 8 11-8M2 20l8-7M24 20l-8-7"/>
        </svg>
        <span>info@corvane.com</span>
      </li>
      <li class="contact-item">
        <svg class="contact-icon" viewBox="0 0 26 26" aria-hidden="true">
          <path d="M13 1a12 12 0 1 0 0 24 12 12 0 0 0 0-24zm-3 5 4 1-1 3 3 2-2 3-3-1-1 4-3-3 1-4-2-2zm7 9 3 1-1 4-3 2 1-4z"/>
        </svg>
        <span>www.corvane.com</span>
      </li>
    </ul>
  </div>
</div>
</body>
</html>
```